Varnex Consulting Business card design.

See our website www.varnexconsulting.example which will give you a good idea of what we are about. The font is called 'Play'.

I'd like a standout business card in keeping with the themes and branding on the website

Target Market(s)

professionals. HR directors

Industry/Entity Type

Business

Contact Information for Business Card

Varnex Consulting PO Box 3172 Merrowdale NSW 2291 1300 485 193 Gavin Threlkeld Principal email: career@varnexconsulting.example ABN: 71203948865

Font styles to use
Other font styles liked:
• Play

Requirements
Must have
• Must have same design colours and branding as website.
• On back I'd prefer a list of the things we do which appears below the name at the header on the website

```html
<!DOCTYPE html>
<html lang="en">
<head>
<meta charset="utf-8">
<title>Varnex Consulting — Business Card</title>
<link href="https://fonts.googleapis.com/css2?family=Play:wght@400;700&display=swap" rel="stylesheet">
<style>
  :root {
    --navy: #132a3e;
    --blue: #2b95dd;
    --paper: #f7f7f7;
    --backdrop: #a9a6a6;
    --white: #ffffff;
  }
  * { margin: 0; padding: 0; box-sizing: border-box; }
  html, body { width: 1200px; height: 1200px; overflow: hidden; }
  body {
    background: var(--backdrop);
    font-family: 'Play', sans-serif;
    position: relative;
  }
  .card {
    position: absolute;
    left: 244px;
    width: 712px;
    height: 420px;
    overflow: hidden;
  }
  .card--front { top: 118px; background: var(--navy); }
  .card--back { top: 648px; background: var(--paper); }

  .company-name {
    position: absolute;
    font-weight: 700;
    line-height: 1;
    white-space: nowrap;
  }
  .card--front .company-name {
    left: 0; right: 0; top: 132px;
    text-align: center;
    font-size: 46px;
    color: var(--white);
  }
  .card--back .company-name {
    left: 48px; top: 48px;
    font-size: 36px;
    color: var(--navy);
  }
  .services {
    position: absolute;
    color: var(--blue);
    white-space: nowrap;
    line-height: 1;
  }
  .card--front .services {
    left: 0; right: 0; top: 214px;
    text-align: center;
    font-size: 16px;
  }
  .card--back .services {
    left: 48px; top: 104px;
    font-size: 14px;
  }
  .website {
    position: absolute;
    left: 0; right: 0; top: 350px;
    display: flex;
    justify-content: center;
    align-items: center;
    gap: 14px;
    font-size: 18px;
    color: var(--white);
    line-height: 1;
  }
  .website__rule { width: 34px; height: 2px; background: var(--blue); }
  .website__domain { color: var(--blue); }

  .contact {
    position: absolute;
    left: 333px;
    top: 178px;
    color: var(--navy);
  }
  .contact__name { font-size: 25px; font-weight: 700; line-height: 1; }
  .contact__role { font-size: 17px; margin-top: 12px; line-height: 1; }
  .contact__list { list-style: none; margin-top: 20px; font-size: 18px; line-height: 24px; }
  .contact__item { display: flex; align-items: center; gap: 18px; }
  .contact__icon { width: 18px; height: 18px; flex: none; }

  .footer-band { position: absolute; left: 0; top: 364px; width: 712px; height: 56px; }
  .abn {
    position: absolute;
    left: 333px; top: 382px;
    font-size: 18px;
    color: var(--white);
    line-height: 1;
  }
</style>
</head>
<body>
  <section class="card card--front">
    <div class="company-name">Varnex Consulting</div>
    <div class="services">Search &amp; Select · Career · Coaching · Leadership · Outplacement</div>
    <div class="website">
      <span class="website__rule"></span>
      <span>www.<span class="website__domain">varnexconsulting</span>.example</span>
      <span class="website__rule"></span>
    </div>
  </section>

  <section class="card card--back">
    <div class="company-name">Varnex Consulting</div>
    <div class="services">Search &amp; Select · Career · Coaching · Leadership · Outplacement</div>

    <div class="contact">
      <div class="contact__name">Gavin Threlkeld</div>
      <div class="contact__role">Principal</div>
      <ul class="contact__list">
        <li class="contact__item">
          <svg class="contact__icon" viewBox="0 0 18 18" aria-hidden="true">
            <path d="M2 6 Q9 1 16 6 L14 8 L12 6.5 L6 6.5 L4 8 Z" fill="var(--blue)"/>
            <rect x="3" y="9" width="12" height="7" rx="1.5" fill="var(--blue)"/>
            <circle cx="9" cy="12.5" r="1.8" fill="var(--paper)"/>
          </svg>
          <span>1300 485 193</span>
        </li>
        <li class="contact__item">
          <svg class="contact__icon" viewBox="0 0 18 18" aria-hidden="true">
            <circle cx="9" cy="9" r="7" fill="var(--blue)"/>
            <g fill="none" stroke="var(--paper)" stroke-width="1">
              <ellipse cx="9" cy="9" rx="3" ry="7"/>
              <line x1="2" y1="9" x2="16" y2="9"/>
              <line x1="3" y1="5.5" x2="15" y2="5.5"/>
              <line x1="3" y1="12.5" x2="15" y2="12.5"/>
            </g>
          </svg>
          <span>career@varnexconsulting.example</span>
        </li>
        <li>PO Box 3172 Merrowdale NSW 2291</li>
      </ul>
    </div>

    <svg class="footer-band" viewBox="0 0 712 56" aria-hidden="true">
      <polygon points="0,27 270,27 251,56 0,56" fill="var(--blue)"/>
      <polygon points="288,0 712,0 712,56 251,56" fill="var(--navy)"/>
    </svg>
    <div class="abn">ABN: 71203948865</div>
  </section>
</body>
</html>
```